Business Card Design

New business card design

Target Market(s)

Residential & Commercial Property Managers

Industry/Entity Type

Plumbing Services

Contact Information for Business Card

Name - Rowan Keddle, title - Director, Phone Number - 0431 286 517, email - rowan@tbk-plumbing.com.au, Company ABN - 73 215 904 386,

Font styles to use
Sans Serif

Colors
0054AA
0677BA
7BADD7
CADEEF
E8F1F8

```html
<!DOCTYPE html>
<html lang="en">
<head>
<meta charset="utf-8">
<title>TBK Plumbing Services – Business Card</title>
<link rel="stylesheet" href="https://fonts.googleapis.com/css2?family=Montserrat:wght@400;500;700&display=swap">
<style>
  :root {
    --stage: #232323;
    --card: #ffffff;
    --ink: #1d2329;
    --wave-blue: #2ca9e1;
    --on-blue: #ffffff;
    --shadow: rgba(0, 0, 0, 0.45);
  }
  * { box-sizing: border-box; margin: 0; padding: 0; }
  html, body {
    width: 1200px;
    height: 780px;
    overflow: hidden;
    background: var(--stage);
    font-family: "Montserrat", Arial, sans-serif;
  }
  .canvas {
    width: 1200px;
    height: 780px;
    display: flex;
    align-items: center;
    justify-content: center;
    gap: 40px;
  }
  .card {
    position: relative;
    width: 560px;
    height: 340px;
    background: var(--card);
    border-radius: 22px;
    overflow: hidden;
    box-shadow: 0 14px 30px var(--shadow);
  }
  .wave {
    position: absolute;
    inset: 0;
    width: 560px;
    height: 340px;
    z-index: 0;
  }
  .wave-fill { fill: var(--wave-blue); }
  .wave-edge, .divider {
    fill: none;
    stroke: var(--on-blue);
    stroke-width: 1.6;
  }
  .brand {
    position: absolute;
    z-index: 1;
    display: flex;
    align-items: center;
    gap: 12px;
    color: var(--ink);
    font-weight: 500;
    white-space: nowrap;
  }
  .brand-dot {
    flex: none;
    border-radius: 50%;
    background: var(--wave-blue);
  }
  .card-front .brand {
    left: 0; right: 0; top: 0; bottom: 0;
    justify-content: center;
    font-size: 30px;
  }
  .card-front .brand-dot { width: 22px; height: 22px; }
  .card-back .brand {
    right: 60px;
    top: 40px;
    font-size: 20px;
  }
  .card-back .brand-dot { width: 14px; height: 14px; }
  .contact {
    position: absolute;
    z-index: 1;
    color: var(--on-blue);
    white-space: nowrap;
  }
  .person { left: 40px; top: 230px; }
  .person-name { font-size: 20px; font-weight: 700; line-height: 1.15; }
  .person-title { font-size: 14px; font-weight: 400; margin-left: 8px; line-height: 1.3; }
  .lines { left: 40px; top: 294px; font-size: 14px; line-height: 20px; }
  .line { display: flex; align-items: center; gap: 8px; }
  .line svg { width: 13px; height: 13px; fill: none; stroke: var(--on-blue); stroke-width: 1.6; }
  .abn {
    right: 40px;
    top: 254px;
    font-size: 14px;
    line-height: 18px;
  }
</style>
</head>
<body>
<main class="canvas">
  <section class="card card-front" aria-label="Card front">
    <div class="brand"><span class="brand-dot"></span><span>tbk plumbing services</span></div>
  </section>

  <section class="card card-back" aria-label="Card back">
    <svg class="wave" viewBox="0 0 560 340" aria-hidden="true">
      <path class="wave-fill" d="M0,250 C140,185 330,172 440,138 C500,118 535,92 560,58 L560,340 L0,340 Z"/>
      <path class="wave-edge" d="M30,240 C160,186 340,176 448,146 C505,128 538,104 560,76"/>
      <path class="divider" d="M40,286 L232,286 Q244,286 250,276 L262,252 Q268,244 282,244 L520,244"/>
    </svg>

    <div class="brand"><span class="brand-dot"></span><span>tbk plumbing services</span></div>

    <div class="contact person">
      <div class="person-name">Rowan Keddle</div>
      <div class="person-title">Director</div>
    </div>

    <div class="contact lines">
      <div class="line">
        <svg viewBox="0 0 14 14"><path d="M3 1.5 L5.5 4 L4 5.5 Q5.5 8.5 8.5 10 L10 8.5 L12.5 11 L11 12.5 Q5 12 1.5 3 Z"/></svg>
        <span>0431 286 517</span>
      </div>
      <div class="line">
        <svg viewBox="0 0 14 14"><rect x="1.5" y="3" width="11" height="8"/><path d="M1.5 3 L7 8 L12.5 3"/></svg>
        <span>rowan@tbk-plumbing.com.au</span>
      </div>
    </div>

    <div class="contact abn">Company ABN - 73 215 904 386</div>
  </section>
</main>
</body>
</html>
```